Modern Business Card

Modern professional business card with more than just logo and demographic info. Something memorable.

We are a trendy/modern chiropractic group with an emphasis on neurology, hence the minimalist-type brain logo. We want to convey that modern and technical aspect with professionalism and the elite nature of our practice environment.

```html
<!DOCTYPE html>
<html lang="en">
<head>
<meta charset="utf-8">
<title>Meridian Spine Care – Business Card</title>
<link rel="stylesheet" href="https://fonts.googleapis.com/css2?family=Marcellus&family=Montserrat:wght@400;500&display=swap">
<style>
  :root {
    --backdrop: #2b2d30;
    --card-white: #ffffff;
    --card-shade: #ececec;
    --brand-blue: #3f73b8;
    --brand-blue-deep: #2f5c99;
    --ink: #1d1d1d;
    --ink-soft: #555a60;
    --rule: #6b6e72;
    --back-mark: #d4d8de;
  }
  * { box-sizing: border-box; margin: 0; padding: 0; }
  html, body {
    width: 1200px; height: 900px; overflow: hidden;
    background: var(--backdrop);
  }
  .stage {
    position: relative; width: 1200px; height: 900px;
    display: flex; flex-direction: column; align-items: center;
    justify-content: center; gap: 48px;
  }
  .card {
    position: relative; width: 640px; height: 366px;
    border-radius: 3px; overflow: hidden;
    box-shadow: 0 10px 28px rgba(0,0,0,.45);
  }

  /* Front */
  .card--front {
    background: radial-gradient(ellipse at 65% 55%, var(--card-white) 45%, var(--card-shade) 100%);
  }
  .holder {
    position: absolute; left: 0; top: 58px;
    padding-left: 34px;
  }
  .holder__bar {
    position: absolute; left: 0; top: 2px;
    width: 9px; height: 26px; background: var(--brand-blue);
  }
  .holder__name {
    font-family: "Marcellus", serif; font-size: 22px;
    letter-spacing: .5px; color: var(--brand-blue);
    text-transform: uppercase; line-height: 30px;
  }
  .holder__role {
    font-family: "Montserrat", sans-serif; font-size: 13px;
    color: var(--ink-soft); margin-top: 2px;
  }
  .divider {
    position: absolute; left: 30px; top: 128px;
    width: 440px; height: 1.5px; background: var(--rule);
  }
  .contact {
    position: absolute; left: 34px; top: 146px;
    list-style: none;
    font-family: "Montserrat", sans-serif; font-size: 14px;
    color: var(--ink-soft);
  }
  .contact li { display: flex; align-items: center; gap: 10px; height: 26px; }
  .contact svg { width: 12px; height: 12px; fill: none; stroke: var(--brand-blue); stroke-width: 1.6; }
  .contact .web-accent { color: var(--brand-blue); }

  .brand {
    position: absolute; right: 44px; top: 56px;
    display: flex; align-items: center; gap: 14px;
  }
  .brand__square { width: 22px; height: 22px; background: var(--brand-blue); }
  .brand__name {
    font-family: "Marcellus", serif; font-size: 24px;
    color: var(--ink); text-transform: uppercase; letter-spacing: 1px;
  }

  .address {
    position: absolute; right: 170px; top: 146px;
    font-family: "Montserrat", sans-serif; font-size: 14px;
    color: var(--ink-soft); text-align: right; line-height: 24px;
  }

  /* Back */
  .card--back {
    background: linear-gradient(160deg, var(--brand-blue-deep) 0%, var(--brand-blue) 70%, #4a7fc4 100%);
    display: flex; align-items: center; justify-content: center; gap: 20px;
  }
  .back-mark__square { width: 38px; height: 38px; background: var(--back-mark); }
  .back-mark__name {
    font-family: "Marcellus", serif; font-size: 42px;
    color: var(--back-mark); text-transform: uppercase; letter-spacing: 2px;
  }
</style>
</head>
<body>
<main class="stage">
  <section class="card card--front" aria-label="Business card front">
    <div class="holder">
      <span class="holder__bar"></span>
      <h1 class="holder__name">Daniel Whitford</h1>
      <p class="holder__role">Director</p>
    </div>

    <div class="brand">
      <span class="brand__square"></span>
      <span class="brand__name">Meridian Spine Care</span>
    </div>

    <div class="divider"></div>

    <ul class="contact">
      <li>
        <svg viewBox="0 0 12 12" aria-hidden="true"><path d="M2.5 1.5 L4.5 1.5 L5.3 4 L4 5 Q5 7.2 7 8 L8 6.7 L10.5 7.5 L10.5 9.5 Q6 10.5 2.5 6 Q1.8 3.5 2.5 1.5Z"/></svg>
        (555) 014-2287
      </li>
      <li>
        <svg viewBox="0 0 12 12" aria-hidden="true"><rect x="1" y="2.5" width="10" height="7"/><path d="M1 2.5 L6 6.5 L11 2.5"/></svg>
        hello@meridianspine.com
      </li>
      <li>
        <svg viewBox="0 0 12 12" aria-hidden="true"><circle cx="6" cy="6" r="5"/><path d="M1 6 H11 M6 1 Q3 6 6 11 Q9 6 6 1"/></svg>
        <span>www.<span class="web-accent">meridianspine</span>.com</span>
      </li>
    </ul>

    <address class="address" style="font-style:normal">
      1187 Larkfield Row<br>
      Corvallis, OR 97330
    </address>
  </section>

  <section class="card card--back" aria-label="Business card back">
    <span class="back-mark__square"></span>
    <span class="back-mark__name">Meridian Spine Care</span>
  </section>
</main>
</body>
</html>
```